Risk Management Company in need of Business Card Design

We sell risk management insurance to Lenders (Banks, Credit Unions, Real Estate Trust).

We need a very clean, professional card that will leave a great impression.

We are looking to use a blue color for our logo on the card (Preferably close to royal blue but are open to looking at navy blue or any darker blues as well).

Please see the logo attached to get an idea. We are open to writing Harbor Ledger Under the logo or next to the logo. Really whatever looks best.

Target Market(s)

Banks, Credit Unions, Real Estate Trusts

Industry/Entity Type

Insurance

Contact Information for Business Card

Name: Tom Brandish
Title: Regional Sales Director
Email: tbrandish@harborledger-example.net
C:410-555-0137
D:410-555-0182
888-555-0149 Ext.318
F:443-555-0164 (We would like to see some cards without the fax number as well to compare)

Company Name: Harbor Ledger
Website: www.harborledger-example.net

Address: 718 E. Marlow St. Suite 340, Alder Falls, OH 21287 (Preferably written on the bottom of the card in small print.)

Colors
0355a3
0455a3

Requirements
Nice to have
• We would like to see a couple of where the back has the logo in reverse colors (Logo White, Background Blue)

```html
<!DOCTYPE html>
<html lang="en">
<head>
<meta charset="utf-8">
<title>Harbor Ledger — Business Cards</title>
<link rel="stylesheet" href="https://fonts.googleapis.com/css2?family=Cinzel:wght@600&family=Libre+Baskerville:wght@400;700&display=swap">
<style>
  :root {
    --navy: #0e1b60;
    --royal: #0355a3;
    --paper: #ffffff;
    --backdrop: #e6e7ea;
  }
  * { box-sizing: border-box; margin: 0; padding: 0; }
  html, body { width: 1200px; height: 900px; overflow: hidden; }
  body {
    background: var(--backdrop);
    position: relative;
    font-family: "Libre Baskerville", Georgia, serif;
  }
  .card {
    position: absolute;
    width: 520px;
    height: 297px;
    overflow: hidden;
    box-shadow: 0 6px 18px rgba(0,0,0,.18);
  }
  .card--front { left: 70px; top: 110px; background: var(--navy); }
  .card--back { left: 610px; top: 110px; background: var(--paper); }
  .card--back-fax { left: 340px; top: 490px; background: var(--paper); }

  .card__bands { position: absolute; inset: 0; width: 100%; height: 100%; }

  .brand {
    font-family: "Cinzel", "Times New Roman", serif;
    font-weight: 600;
    letter-spacing: 1px;
    white-space: nowrap;
  }
  .card--front .brand {
    position: absolute; left: 34px; top: 150px;
    font-size: 30px; color: var(--paper);
  }
  .website {
    position: absolute; right: 30px; top: 208px;
    font-size: 12px; color: var(--paper);
    white-space: nowrap;
  }

  .card--back .brand, .card--back-fax .brand {
    position: absolute; left: 26px; top: 132px;
    font-size: 22px; color: var(--navy);
  }
  .contact {
    position: absolute; left: 268px; top: 46px; right: 10px;
    color: var(--royal);
  }
  .contact__name {
    font-size: 19px; font-weight: 700; letter-spacing: .5px;
    text-transform: uppercase; color: var(--navy);
  }
  .contact__title { font-size: 9px; margin: 2px 0 16px 2px; color: var(--royal); }
  .contact__list { list-style: none; font-size: 10px; line-height: 16px; }
  .contact__list li { display: flex; align-items: flex-start; gap: 6px; white-space: nowrap; }
  .contact__list svg { width: 10px; height: 10px; margin-top: 3px; flex: none; fill: var(--navy); }
  .contact__list .no-icon { padding-left: 16px; }
</style>
</head>
<body>

  <!-- Front: brand on navy -->
  <section class="card card--front" aria-label="Card front">
    <svg class="card__bands" viewBox="0 0 520 297" preserveAspectRatio="none" aria-hidden="true">
      <polygon points="240,30 520,10 520,24 240,44" fill="#ffffff"/>
      <polygon points="0,258 260,236 260,248 0,270" fill="#ffffff"/>
    </svg>
    <div class="brand">Harbor Ledger</div>
    <div class="website">www.harborledger-example.net</div>
  </section>

  <!-- Back: contact details -->
  <section class="card card--back" aria-label="Card back">
    <svg class="card__bands" viewBox="0 0 520 297" preserveAspectRatio="none" aria-hidden="true">
      <rect x="0" y="0" width="520" height="8" fill="#0e1b60"/>
      <rect x="0" y="284" width="520" height="13" fill="#0e1b60"/>
    </svg>
    <div class="brand">Harbor Ledger</div>
    <div class="contact">
      <div class="contact__name">Tom Brandish</div>
      <div class="contact__title">Regional Sales Director</div>
      <ul class="contact__list">
        <li><svg viewBox="0 0 10 10"><path d="M1 3 Q5 0 9 3 L8 4.5 L6.5 3.5 L3.5 3.5 L2 4.5Z M2 5 H8 V9 H2Z"/></svg>410-555-0182/888-555-0149 Ext.318</li>
        <li><svg viewBox="0 0 10 10"><path d="M0 2 H10 V8 H0Z M0.8 2.6 L5 5.6 L9.2 2.6" stroke="#fff" stroke-width=".6"/></svg>tbrandish@harborledger-example.net</li>
        <li><svg viewBox="0 0 10 10"><path d="M3 0 H7 V10 H3Z M3.8 1 V8 H6.2 V1Z" fill-rule="evenodd"/></svg>410-555-0137</li>
        <li><svg viewBox="0 0 10 10"><path d="M5 0 L10 5 H8.5 V10 H6 V7 H4 V10 H1.5 V5 H0Z"/></svg>718 E. Marlow St. Suite 340,</li>
        <li class="no-icon">Alder Falls, OH 21287</li>
      </ul>
    </div>
  </section>

  <!-- Back: contact details with fax -->
  <section class="card card--back-fax" aria-label="Card back with fax">
    <svg class="card__bands" viewBox="0 0 520 297" preserveAspectRatio="none" aria-hidden="true">
      <rect x="0" y="0" width="520" height="8" fill="#0e1b60"/>
      <rect x="0" y="284" width="520" height="13" fill="#0e1b60"/>
    </svg>
    <div class="brand">Harbor Ledger</div>
    <div class="contact">
      <div class="contact__name">Tom Brandish</div>
      <div class="contact__title">Regional Sales Director</div>
      <ul class="contact__list">
        <li><svg viewBox="0 0 10 10"><path d="M1 3 Q5 0 9 3 L8 4.5 L6.5 3.5 L3.5 3.5 L2 4.5Z M2 5 H8 V9 H2Z"/></svg>410-555-0182/888-555-0149 Ext.318</li>
        <li><svg viewBox="0 0 10 10"><path d="M0 2 H10 V8 H0Z M0.8 2.6 L5 5.6 L9.2 2.6" stroke="#fff" stroke-width=".6"/></svg>tbrandish@harborledger-example.net</li>
        <li><svg viewBox="0 0 10 10"><path d="M3 0 H7 V10 H3Z M3.8 1 V8 H6.2 V1Z" fill-rule="evenodd"/></svg>410-555-0137</li>
        <li><svg viewBox="0 0 10 10"><path d="M2 0 H8 V3 H2Z M0 3.5 H10 V8 H0Z M2.5 6 H7.5 V10 H2.5Z"/></svg>443-555-0164</li>
        <li><svg viewBox="0 0 10 10"><path d="M5 0 L10 5 H8.5 V10 H6 V7 H4 V10 H1.5 V5 H0Z"/></svg>718 E. Marlow St. Suite 340,</li>
        <li class="no-icon">Alder Falls, OH 21287</li>
      </ul>
    </div>
  </section>

</body>
</html>
```